Website redesign for job agency recruitment

Please refer to the attached document, “Tarvenly Work Website Brief,” for comprehensive details regarding the scope, objectives, and requirements of this website redesign project.

For imagery you can use images from this website https://www.pixelmarrowfoto.com or any other you regularly use.

Target Market(s)

Jobseekers and Companies looking for general labour

Industry/Entity Type

Services: Oil, Gas and Mining, Administrative, Construction and Trades, Warehouse and Logistics and, Manufacturing.

Number of Pages Required

5+ page

Font styles to use
Serif
Other font styles liked:
• Inter, Open-Sans or similar.

Requirements
Must have
• The requirements highlighted in the Word document attached. The final design needs to be provided in Figma including all viewports (Desktop, mobiel and tablet)
Should not have
• Website we like as a reference: www.brevicktalentco.com, www.qelvaworks.com, www.zunmarra.com, www.ferrowhires.com, www.9vtalentpool.com, www.hiringwithtrello.ca

```html
<!DOCTYPE html>
<html lang="en">
<head>
<meta charset="utf-8">
<title>Tarvenly Work Ltd. – Recruitment</title>
<link href="https://fonts.googleapis.com/css2?family=Libre+Baskerville:wght@700&family=Poppins:wght@400;500;600&display=swap" rel="stylesheet">
<style>
:root{
  --navy:#0d3a8f;
  --blue:#1a47a8;
  --yellow:#f5bd12;
  --cream:#fbefcf;
  --ink:#111111;
  --text:#333333;
  --grey-bg:#f1f2f4;
  --dark:#1b1c1f;
  --white:#ffffff;
}
*{margin:0;padding:0;box-sizing:border-box}
html,body{width:1200px;height:2754px;overflow:hidden}
body{position:relative;font-family:"Poppins",sans-serif;color:var(--text);background:var(--white)}
.abs{position:absolute}
.serif{font-family:"Libre Baskerville",serif;font-weight:700;color:var(--ink)}

/* hero */
.hero{left:0;top:0;width:1200px;height:736px;background:linear-gradient(160deg,#1c3f78 0%,#2b5c9a 35%,#3f6fa6 55%,#b86a2c 85%,#e0892a 100%)}
.cream-band{left:0;top:736px;width:1200px;height:38px;background:var(--cream)}
.logo-plate{left:139px;top:0;width:211px;height:209px;background:var(--white);border-radius:0 0 105px 105px;display:flex;flex-direction:column;align-items:center;justify-content:center;padding-top:10px}
.logo-plate .mark{width:44px;height:44px;border-radius:50%;background:var(--navy);margin-bottom:10px}
.logo-plate .name{font-size:17px;font-weight:600;color:var(--navy)}
.logo-plate .tag{font-size:9px;font-style:italic;color:#777;margin-top:4px}
.phone{left:630px;top:21px;display:flex;align-items:center;gap:14px;color:var(--white)}
.phone .icon{width:44px;height:44px;border-radius:50%;background:var(--yellow);display:flex;align-items:center;justify-content:center}
.phone small{display:block;font-size:12px}
.phone b{font-size:17px;font-weight:500}
.btn{display:flex;align-items:center;justify-content:center;font-size:15px;font-weight:500;text-decoration:none}
.btn-yellow{background:var(--yellow);color:var(--ink)}
.btn-blue{background:var(--blue);color:var(--white)}
.reg{left:871px;top:22px;width:184px;height:43px}
.nav{left:442px;top:96px;width:643px;height:45px;border-bottom:1px solid rgba(255,255,255,.45);display:flex;gap:26px;justify-content:center;color:var(--white);font-size:15px;font-weight:500}
.hero-title{left:0;top:290px;width:1200px;text-align:center;color:var(--white);font-size:43px;line-height:56px}
.hero-sub{left:0;top:424px;width:1200px;text-align:center;color:var(--white);font-size:16px;font-weight:500}
.hero-btn1{left:414px;top:488px;width:183px;height:43px}
.hero-btn2{left:604px;top:488px;width:183px;height:43px}
.dots{left:1124px;top:349px;display:flex;flex-direction:column;gap:13px}
.dots i{width:8px;height:8px;border-radius:50%;background:var(--white)}
.scroll-btn{left:569px;top:717px;width:62px;height:62px;border-radius:50%;background:var(--white);box-shadow:0 4px 14px rgba(0,0,0,.15);display:flex;align-items:center;justify-content:center}

/* services */
.eyebrow{font-size:18px;font-weight:500;color:var(--navy);letter-spacing:.3px}
.svc-eyebrow{left:0;top:862px;width:1200px;text-align:center}
.svc-title{left:0;top:904px;width:1200px;text-align:center;font-size:40px}
.svc-label{font-size:14px;font-weight:600;color:var(--ink)}
.svc-card{left:742px;top:1274px;width:287px;height:154px;background:var(--white);box-shadow:0 6px 24px rgba(0,0,0,.08);padding:24px 18px}
.svc-card h4{font-size:14px;font-weight:500;color:var(--ink)}
.svc-card p{font-size:13px;line-height:23px;margin-top:10px}
.svc-card a{display:block;font-size:13px;color:var(--navy);margin-top:8px;text-decoration:none}

/* about */
.about{left:0;top:1536px;width:1200px;height:811px;background:linear-gradient(180deg,#eef0f3,#f6f7f8)}
.about-eyebrow{left:673px;top:1642px}
.about-title{left:673px;top:1684px;font-size:40px}
.about-copy{left:673px;top:1758px;width:406px;font-size:13.5px;line-height:25.6px;text-align:justify}
.about-copy p+p{margin-top:25px}
.about-btn{left:673px;top:2072px;width:161px;height:43px}

/* apply + footer */
.cream-band2{left:0;top:2309px;width:1200px;height:38px;background:var(--cream)}
.footer{left:0;top:2347px;width:1200px;height:407px;background:var(--dark)}
.apply{left:158px;top:2212px;width:883px;height:278px;background:var(--yellow);text-align:center}
.apply h2{font-size:40px;margin-top:60px}
.apply p{font-size:17px;color:var(--ink);margin-top:22px}
.apply .btn{width:183px;height:43px;margin:22px auto 0}
.foot-nav{left:0;top:2540px;width:1200px;display:flex;justify-content:center;gap:24px;color:var(--white);font-size:15px;font-weight:500}
.foot-links{left:0;top:2586px;width:1200px;text-align:center;color:var(--white);font-size:15px;font-weight:500}
.foot-line{left:97px;top:2636px;width:1006px;height:1px;background:rgba(255,255,255,.35)}
.social{top:2615px;width:40px;height:40px;border-radius:50%;background:var(--white)}
.copy{left:0;top:2658px;width:1200px;text-align:center;color:var(--white);font-size:15px;font-weight:500}
</style>
</head>
<body>

<section>
  <div class="abs hero" role="img" aria-label="Upward view of a glass office tower at sunset"></div>
  <div class="abs cream-band"></div>

  <div class="abs logo-plate">
    <span class="mark"></span>
    <span class="name">Tarvenly Work Ltd.</span>
    <span class="tag">The right people to power your business</span>
  </div>

  <div class="abs phone">
    <span class="icon">
      <svg width="18" height="18" viewBox="0 0 24 24"><path fill="#111" d="M6.6 10.8a15.1 15.1 0 0 0 6.6 6.6l2.2-2.2a1 1 0 0 1 1-.25 11.4 11.4 0 0 0 3.6.57 1 1 0 0 1 1 1V20a1 1 0 0 1-1 1A17 17 0 0 1 3 4a1 1 0 0 1 1-1h3.5a1 1 0 0 1 1 1c0 1.25.2 2.45.57 3.6a1 1 0 0 1-.25 1z"/></svg>
    </span>
    <span><small>Toll Free</small><b>1-800-555-0147</b></span>
  </div>
  <a class="abs btn btn-yellow reg">Client Registration</a>

  <nav class="abs nav">
    <span>Home</span><span>About Us</span><span>Services</span><span>Candidates</span><span>Employers</span><span>Contact Us</span>
    <svg width="15" height="15" viewBox="0 0 24 24" style="margin-top:4px"><circle cx="10" cy="10" r="7" fill="none" stroke="#fff" stroke-width="3"/><path d="M15 15l6 6" stroke="#fff" stroke-width="3"/></svg>
  </nav>

  <h1 class="abs serif hero-title" style="color:var(--white)">WHERE SKILLED TALENT MEETS<br>INDUSTRY DEMAND</h1>
  <p class="abs hero-sub">Specialized recruitment solutions tailored for Canada’s key industries.</p>
  <a class="abs btn btn-yellow hero-btn1">For Candidates</a>
  <a class="abs btn btn-blue hero-btn2">For Employers</a>
  <div class="abs dots"><i></i><i></i><i></i></div>
  <div class="abs scroll-btn">
    <svg width="16" height="16" viewBox="0 0 16 16"><path d="M3 3l5 5 5-5M3 8l5 5 5-5" fill="none" stroke="#111" stroke-width="1.8"/></svg>
  </div>
</section>

<section>
  <p class="abs eyebrow svc-eyebrow">OUR SERVICES</p>
  <h2 class="abs serif svc-title">WHAT WE OFFER</h2>

  <svg class="abs" style="left:0;top:0" width="1200" height="1500" viewBox="0 0 1200 1500">
    <path d="M302 1021 Q360 1025 394 1048 Q440 1080 449 1129 Q475 1170 468 1218 Q465 1265 449 1306 Q420 1360 380 1381 Q340 1398 302 1400" fill="none" stroke="#0d3a8f" stroke-width="2.5"/>
    <circle cx="302" cy="1021" r="9" fill="#f5bd12"/>
    <circle cx="302" cy="1400" r="9" fill="#f5bd12"/>
    <circle cx="275" cy="1211" r="121" fill="#fff" stroke="#0d3a8f" stroke-width="1.2"/>
    <circle cx="275" cy="1211" r="117" fill="none" stroke="#0d3a8f" stroke-width=".6"/>
    <circle cx="394" cy="1048" r="33" fill="#0d3a8f"/>
    <circle cx="449" cy="1129" r="33" fill="#f5bd12"/>
    <circle cx="468" cy="1218" r="33" fill="#0d3a8f"/>
    <circle cx="449" cy="1306" r="33" fill="#0d3a8f"/>
    <circle cx="380" cy="1381" r="33" fill="#0d3a8f"/>
    <path d="M946 992 A198 198 0 0 1 1000 1371" fill="none" stroke="#0d3a8f" stroke-width="13"/>
    <path d="M745 1130 A198 198 0 0 0 748 1275" fill="none" stroke="#f5bd12" stroke-width="4"/>
  </svg>
  <div class="abs" style="left:199px;top:1201px;font-size:19px;font-weight:600;color:var(--navy)">Tarvenly Work</div>

  <span class="abs svc-label" style="left:443px;top:1033px">OIL, GAS &amp; MINING</span>
  <span class="abs svc-label" style="left:495px;top:1115px">ADMINISTRATIVE</span>
  <span class="abs svc-label" style="left:523px;top:1204px">CONSTRUCTION &amp; TRADES</span>
  <span class="abs svc-label" style="left:503px;top:1292px">WAREHOUSE &amp; LOGISTICS</span>
  <span class="abs svc-label" style="left:432px;top:1367px">MANUFACTURING</span>

  <div class="abs" role="img" aria-label="Portrait of a smiling office professional in a mustard blazer" style="left:746px;top:987px;width:394px;height:394px;border-radius:50%;background:radial-gradient(circle at 50% 45%,#b9865a,#6f8a7c 60%,#3c5a4f)"></div>
  <div class="abs svc-card">
    <h4>ADMINISTRATIVE</h4>
    <p>Lorem ipsum dolor sit amet, consectetur adipiscing Lorem ipsum dolor</p>
    <a>Learn More</a>
  </div>
</section>

<section>
  <div class="abs about"></div>
  <svg class="abs" style="left:0;top:0" width="1200" height="2200" viewBox="0 0 1200 2200">
    <path d="M359 1664 A219 219 0 0 0 140 1883 A219 219 0 0 0 359 2102" fill="none" stroke="#1a47a8" stroke-width="14" transform="translate(-2 5)"/>
    <path d="M359 2110 A219 219 0 0 0 578 1891 L578 1870" fill="none" stroke="#f5bd12" stroke-width="10" transform="translate(2 0)"/>
  </svg>
  <div class="abs" role="img" aria-label="Group of smiling colleagues in an office" style="left:142px;top:1666px;width:434px;height:434px;border-radius:50%;background:radial-gradient(circle at 50% 45%,#d6b49a,#7c8ea0 60%,#3d4c5e)"></div>

  <p class="abs eyebrow about-eyebrow">ABOUT US</p>
  <h2 class="abs serif about-title">WHO WE ARE</h2>
  <div class="abs about-copy">
    <p>Tarvenly Work offers a complete range of staffing services to keep pace with your career or operational demands. We understand it’s not only daunting but very costly in both time and money to make your business thrive in a rapidly changing environment.</p>
    <p>Our staffing and recruitment services are not just limited to finding good people. We are a Canada-wide team of capable search specialists, career counselors, HR specialists, and business consultants who enjoy providing our clients with a very customized staffing solution that evolves</p>
  </div>
  <a class="abs btn btn-yellow about-btn">Learn More</a>
</section>

<footer>
  <div class="abs cream-band2"></div>
  <div class="abs footer"></div>
  <div class="abs apply">
    <h2 class="serif">APPLY NOW</h2>
    <p>Tarvenly Work offer various opportunities in the different industries.</p>
    <a class="btn btn-blue">Apply Here</a>
  </div>
  <nav class="abs foot-nav">
    <span>Home</span><span>About Us</span><span>Services</span><span>Candidates</span><span>Employers</span><span>Contact Us</span>
    <svg width="15" height="15" viewBox="0 0 24 24" style="margin-top:4px"><circle cx="10" cy="10" r="7" fill="none" stroke="#fff" stroke-width="3"/><path d="M15 15l6 6" stroke="#fff" stroke-width="3"/></svg>
  </nav>
  <p class="abs foot-links">Terms of Use &nbsp;|&nbsp; Manufacturing &nbsp;|&nbsp; Vancouver Location</p>
  <div class="abs foot-line"></div>
  <span class="abs social" style="left:913px" aria-label="Social profile"></span>
  <span class="abs social" style="left:962px" aria-label="Social profile"></span>
  <p class="abs copy">© Tarvenly Work Ltd. | All rights reserved 2026</p>
</footer>

</body>
</html>
```